Very visible CoWorking Building Sign overlooking downtown LA and 110 freeway

Our building is drab but very visible and in the best location. We need a great sign for our monolith that overlooks downtown LA and the 100 freeway. We are a new CoWorking business and would like to have a few things we do on the sign: private offices, virtual offices, CoWorking Lounge. Everything we have seen is ho-hum. Can you get us noticed? We need people to know what we do and that we are here but in a creative, professional, unique sign.
Target Market(s)
People who have a business in DTLA, remote workers and those who work from home who need a professional address.
Requirements
Must have
- Our logo (which can be somewhat reimagined) which has our address 2417 on it. The three things we focus on: Private Offices, Virtual Offices, CoWorking Lounge. Incorporate some Navy. Readable from several hundred feet away.
Nice to have
- Mural feel? Something inspirational in this crazy COVID times? Graphics? Color block. I like the idea of decorative but it has to be readable as a building sign. The same with the use of colors. Our colors are grays and navy but with a pop of the chartreuse (we have 2 velvet chartreuse chairs in the space). Helpful to view our website: Harborview2417.com.
Should not have
- Not too graffiti. Keep it professional but unique and wow.

```html
<!DOCTYPE html>
<html lang="en">
<head>
<meta charset="utf-8">
<title>Harborview2417.com – Building Sign</title>
<link href="https://fonts.googleapis.com/css2?family=Montserrat:wght@700;800&family=Vidaloka&display=swap" rel="stylesheet">
<style>
  :root {
    --navy: #033d79;
    --green-light: #9bcb3c;
    --green-dark: #76a910;
    --mustard: #cbb400;
    --white: #ffffff;
    --backdrop-start: #333333;
    --backdrop-end: #8a8a8a;
  }
  html, body {
    margin: 0;
    padding: 0;
    width: 982px;
    height: 1200px;
    overflow: hidden;
  }
  body {
    background: linear-gradient(135deg, var(--backdrop-start), var(--backdrop-end));
  }
  .sign {
    display: block;
    width: 982px;
    height: 1200px;
  }
  .panel-navy { fill: var(--navy); }
  .swoosh-dark { fill: var(--green-dark); }
  .swoosh-light { fill: var(--green-light); }
  .swoosh-white { fill: var(--white); }
  .brand-name {
    font-family: "Vidaloka", Georgia, serif;
    fill: var(--navy);
  }
  .service-pill { fill: var(--white); }
  .service-ring { fill: var(--navy); }
  .service-dot { fill: var(--green-light); }
  .service-arrow {
    fill: none;
    stroke: var(--white);
    stroke-width: 14;
    stroke-linecap: round;
    stroke-linejoin: round;
  }
  .service-label {
    font-family: "Montserrat", Arial, sans-serif;
    font-weight: 700;
    font-size: 80px;
    fill: var(--navy);
    letter-spacing: -1px;
  }
  .contact-band { fill: var(--mustard); }
  .contact-number {
    font-family: "Montserrat", Arial, sans-serif;
    font-weight: 800;
    font-size: 116px;
    fill: var(--white);
  }
  .phone-icon { fill: var(--white); }
  .phone-waves {
    fill: none;
    stroke: var(--white);
    stroke-width: 5;
    stroke-linecap: round;
  }
</style>
</head>
<body>
<svg class="sign" viewBox="0 0 1736 2122" xmlns="http://www.w3.org/2000/svg" aria-label="Harborview2417.com building sign">
  <!-- panel -->
  <rect class="panel-navy" x="189" y="212" width="1358" height="1698"/>

  <!-- header swooshes -->
  <path class="swoosh-dark" d="M370 818 C600 900 850 990 1050 993 C1250 995 1400 920 1482 860 C1440 1000 1320 1125 1090 1125 C850 1125 570 980 370 818 Z"/>
  <path class="swoosh-light" d="M189 212 L1433 212 C1490 290 1530 360 1547 395 L1547 780 C1450 930 1250 992 1050 992 C750 995 400 880 189 720 Z"/>
  <path class="swoosh-white" d="M189 212 L1343 212 C1450 350 1515 490 1515 630 C1515 850 1300 985 1040 985 C750 985 420 850 189 657 Z"/>

  <!-- brand name -->
  <g class="brand">
    <text class="brand-name" x="345" y="460" font-size="200">2417</text>
    <text class="brand-name" x="345" y="703" font-size="215" textLength="1045" lengthAdjust="spacingAndGlyphs">Harborview</text>
    <text class="brand-name" x="1390" y="848" font-size="175" text-anchor="end">.com</text>
  </g>

  <!-- services -->
  <g class="service">
    <rect class="service-pill" x="380" y="1168" width="1050" height="126" rx="63"/>
    <circle class="service-ring" cx="376" cy="1232" r="74"/>
    <circle class="service-dot" cx="370" cy="1232" r="72"/>
    <path class="service-arrow" d="M338 1232 H398 M372 1210 L398 1232 L372 1255"/>
    <text class="service-label" x="484" y="1261">PRIVATE OFFICES</text>
  </g>
  <g class="service">
    <rect class="service-pill" x="380" y="1351" width="1050" height="126" rx="63"/>
    <circle class="service-ring" cx="376" cy="1414" r="74"/>
    <circle class="service-dot" cx="370" cy="1414" r="72"/>
    <path class="service-arrow" d="M338 1414 H398 M372 1392 L398 1414 L372 1437"/>
    <text class="service-label" x="486" y="1443">VIRTUAL OFFICES</text>
  </g>
  <g class="service">
    <rect class="service-pill" x="380" y="1533" width="1050" height="126" rx="63"/>
    <circle class="service-ring" cx="376" cy="1596" r="74"/>
    <circle class="service-dot" cx="370" cy="1596" r="72"/>
    <path class="service-arrow" d="M338 1596 H398 M372 1574 L398 1596 L372 1619"/>
    <text class="service-label" x="484" y="1625">COWORKING LOUNGE</text>
  </g>

  <!-- contact band -->
  <rect class="contact-band" x="189" y="1727" width="1358" height="135"/>
  <g class="phone">
    <path class="phone-icon" d="M350 1750 C340 1758 336 1772 342 1790 C352 1815 372 1835 398 1846 C414 1852 428 1848 436 1838 L418 1818 C412 1824 404 1826 396 1822 C382 1814 370 1802 362 1788 C358 1780 360 1772 366 1766 Z"/>
    <path class="phone-waves" d="M394 1776 A12 12 0 0 1 406 1788 M394 1762 A26 26 0 0 1 420 1788 M394 1748 A40 40 0 0 1 434 1788"/>
  </g>
  <text class="contact-number" x="487" y="1837" textLength="913" lengthAdjust="spacingAndGlyphs">+310-555-0142</text>
</svg>
</body>
</html>
```